Card design for orthopaedic surgeons working as The Brightwater Joint Centre

Business cards, letterhead

Colors

Designer to choose colors to be used in the design.

Requirements
Must have
• Late addition.
• Cards letterhead must have logos of
• Crestmoor Lindell College of Surgeons
• Varenwood Bone Health Association
Nice to have
• Back of card to have space for appointment time to be added by hand and some blank space for writing incidental other notes.

```html
<!DOCTYPE html>
<html lang="en">
<head>
<meta charset="utf-8">
<title>The Brightwater Joint Centre – Business Card</title>
<link href="https://fonts.googleapis.com/css2?family=Montserrat:wght@400&family=Open+Sans:wght@400;700&display=swap" rel="stylesheet">
<style>
  :root {
    --bg-top: #b4b4b4;
    --bg-bottom: #e2e4e6;
    --navy: #07334d;
    --sky: #33b2fd;
    --white: #ffffff;
    --ink: #0d3550;
  }
  * { margin: 0; padding: 0; box-sizing: border-box; }
  html, body { width: 1200px; height: 1200px; overflow: hidden; }
  body {
    background: linear-gradient(180deg, var(--bg-top) 0%, var(--bg-bottom) 100%);
    font-family: "Open Sans", Arial, sans-serif;
    position: relative;
  }
  .card {
    position: absolute;
    left: 220px;
    width: 760px;
    height: 430px;
    border-radius: 34px;
    overflow: hidden;
    box-shadow: 0 8px 18px rgba(0,0,0,0.22);
  }
  /* Back of card */
  .card-back {
    top: 130px;
    background: var(--navy);
    display: flex;
    flex-direction: column;
    align-items: center;
    justify-content: center;
    gap: 34px;
  }
  .card-back .brand-name {
    font-family: "Montserrat", sans-serif;
    font-weight: 400;
    font-size: 42px;
    color: var(--sky);
    letter-spacing: -0.5px;
  }
  .card-back .web {
    font-family: "Open Sans", sans-serif;
    font-size: 20px;
    letter-spacing: 7px;
    color: var(--white);
  }
  .card-back .web .domain { color: var(--sky); }

  /* Front of card */
  .card-front {
    top: 640px;
    background: var(--white);
  }
  .card-front .brand-name {
    position: absolute;
    left: 34px;
    top: 196px;
    font-family: "Montserrat", sans-serif;
    font-weight: 400;
    font-size: 26px;
    color: var(--ink);
    letter-spacing: -0.4px;
  }
  .web-strip {
    position: absolute;
    left: 432px;
    top: 62px;
    width: 30px;
    height: 306px;
    background: var(--navy);
  }
  .web-strip span {
    position: absolute;
    left: 50%;
    top: 50%;
    transform: translate(-50%, -50%) rotate(-90deg);
    white-space: nowrap;
    color: var(--white);
    font-size: 17px;
    letter-spacing: 0.5px;
  }
  .contact-panel {
    position: absolute;
    left: 472px;
    top: 62px;
    width: 288px;
    height: 306px;
    background: var(--sky);
    color: var(--white);
    padding: 30px 20px 0 22px;
  }
  .contact-panel .person {
    font-family: Arial, "Open Sans", sans-serif;
    font-weight: 700;
    font-size: 25px;
    line-height: 1.1;
  }
  .contact-panel .role {
    font-size: 19px;
    margin-bottom: 22px;
  }
  .contact-panel .address {
    font-size: 18px;
    line-height: 1.3;
    margin-bottom: 14px;
  }
  .contact-line {
    display: flex;
    align-items: center;
    gap: 10px;
    font-size: 18px;
    line-height: 1.55;
  }
  .contact-line svg { width: 16px; height: 16px; flex: none; }
</style>
</head>
<body>
  <section class="card card-back" aria-label="Back of business card">
    <div class="brand-name">The Brightwater Joint Centre</div>
    <div class="web">www.<span class="domain">brightwaterjoint</span>.com</div>
  </section>

  <section class="card card-front" aria-label="Front of business card">
    <div class="brand-name">The Brightwater Joint Centre</div>
    <div class="web-strip"><span>www.brightwaterjoint.com</span></div>
    <div class="contact-panel">
      <div class="person">Maren Holloway</div>
      <div class="role">Title</div>
      <div class="address">Street Name, City Name<br>Zipcode - 012345</div>
      <div class="contact-line">
        <svg viewBox="0 0 16 16" aria-hidden="true"><circle cx="8" cy="8" r="7" fill="none" stroke="#fff" stroke-width="1.4"/><path d="M5.5 4.5l1.5 1.6-0.8 1.1a5 5 0 0 0 2.6 2.6l1.1-0.8 1.6 1.5-1 1.1c-3 0-6-3-6-6z" fill="#fff"/></svg>
        <span>012-345-6789</span>
      </div>
      <div class="contact-line">
        <svg viewBox="0 0 16 16" aria-hidden="true"><rect x="1.5" y="4" width="13" height="9" rx="1" fill="#fff"/><path d="M1.5 4.5l6.5 5 6.5-5" fill="none" stroke="#33b2fd" stroke-width="1.3"/></svg>
        <span>info@brightwaterjoint.com</span>
      </div>
    </div>
  </section>
</body>
</html>
```